Print materials for 3-star hotel

We are changing up our print materials (notepads, letterheads, key card jackets, small flyer for the room rates) We are a 3 star business hotel in the Philippines and have mainly used grey tones and clean, simple lines. See attached photos for logo and hotel interior photos.

Target Market(s)

Business

Contact Information for Business Card

Corvale Terrace Hotel
Lindwell Banca Avenue corner Tolenta St Cebu City 6000 Philippines
Tel: +63 32 481 7302
Mobile: +63 917 648 2095
www.corvaleterracehotel.example

Font styles to use
Serif
Sans Serif

Requirements
Must have
• Simple
• Readable font and font size
Nice to have
• Neutral colors, grey and taupes
Should not have
• No purples and bright blues

```html
<!DOCTYPE html>
<html lang="en">
<head>
<meta charset="utf-8">
<title>Corvale Terrace Hotel – Business Card</title>
<link rel="stylesheet" href="https://fonts.googleapis.com/css2?family=Cinzel:wght@400&family=Roboto:wght@400&display=swap">
<style>
  :root {
    --backdrop: #2e2e2e;
    --card: #1f1f1f;
    --ink: #f2f2f2;
    --ink-soft: #e4e4e4;
    --shadow: rgba(0,0,0,0.55);
  }
  * { margin: 0; padding: 0; box-sizing: border-box; }
  html, body {
    width: 1200px; height: 960px; overflow: hidden;
    background: var(--backdrop);
  }
  .stage { position: relative; width: 1200px; height: 960px; }
  .card {
    position: absolute;
    width: 600px; height: 343px;
    background: var(--card);
    box-shadow: 0 3px 10px var(--shadow);
    color: var(--ink);
  }
  .card--front { left: 316px; top: 113px; }
  .card--back  { left: 312px; top: 473px; }

  .brand-name {
    position: absolute; left: 41px; top: 52px; width: 220px;
    font-family: 'Cinzel', serif; font-weight: 400;
    font-size: 19px; letter-spacing: 3px; line-height: 30px;
    text-align: center; color: var(--ink);
  }
  .address {
    position: absolute; left: 41px; top: 166px;
    font-family: 'Roboto', sans-serif; font-size: 14.5px; line-height: 18px;
    color: var(--ink-soft);
  }
  .contacts {
    position: absolute; left: 41px; top: 213px; list-style: none;
    font-family: 'Roboto', sans-serif; font-size: 14.5px; line-height: 19px;
    color: var(--ink-soft);
  }
  .contacts li { display: flex; align-items: center; }
  .contacts svg { width: 14px; height: 14px; margin-right: 9px; fill: var(--ink); flex: none; }
  .person {
    position: absolute; right: 44px; top: 215px; text-align: right;
  }
  .person__name {
    font-family: 'Cinzel', serif; font-size: 23px; letter-spacing: 0.5px; line-height: 28px;
  }
  .person__title {
    font-family: 'Roboto', sans-serif; font-size: 14.5px; line-height: 16px;
  }
  .accent-bar {
    position: absolute; right: 2px; top: 217px; width: 12px; height: 39px;
    background: var(--ink);
  }

  .back-name {
    position: absolute; left: 0; right: 0; top: 150px; text-align: center;
    font-family: 'Cinzel', serif; font-weight: 400; font-size: 28px; letter-spacing: 5px;
    color: var(--ink);
  }
  .back-web {
    position: absolute; left: 0; right: 0; top: 284px; text-align: center;
    font-family: 'Roboto', sans-serif; font-size: 15px; letter-spacing: 5px;
    color: var(--ink-soft);
  }
</style>
</head>
<body>
<main class="stage">
  <section class="card card--front">
    <div class="brand-name">Corvale Terrace<br>Hotel</div>
    <p class="address">Lindwell Banca Ave cor. Tolenta St<br>Cebu City 6000 Philippines</p>
    <ul class="contacts">
      <li><svg viewBox="0 0 24 24"><path d="M6.6 10.8a15.1 15.1 0 0 0 6.6 6.6l2.2-2.2c.3-.3.7-.4 1-.2 1.1.4 2.3.6 3.6.6.6 0 1 .4 1 1V20c0 .6-.4 1-1 1A17 17 0 0 1 3 4c0-.6.4-1 1-1h3.5c.6 0 1 .4 1 1 0 1.3.2 2.5.6 3.6.1.3 0 .7-.2 1z"/></svg>+63 32 481 7302</li>
      <li><svg viewBox="0 0 24 24"><path d="M7 1h10a2 2 0 0 1 2 2v18a2 2 0 0 1-2 2H7a2 2 0 0 1-2-2V3a2 2 0 0 1 2-2zm0 3v14h10V4zm5 15.5a1 1 0 1 0 0 2 1 1 0 0 0 0-2z"/></svg>+63 917 648 2095</li>
      <li><svg viewBox="0 0 24 24"><path d="M6 2h10l2 2v4H6zM3 9h18a1 1 0 0 1 1 1v8h-4v4H6v-4H2v-8a1 1 0 0 1 1-1zm5 7v4h8v-4z"/></svg>+63 32 481 7310</li>
      <li><svg viewBox="0 0 24 24"><path d="M2 5h20v14H2zm2 2v.5l8 5 8-5V7zm0 2.8V17h16V9.8l-8 5z"/></svg>stay@corvaleterrace.example</li>
      <li><svg viewBox="0 0 24 24"><path d="M12 2a10 10 0 1 0 0 20 10 10 0 0 0 0-20zm-1 17.9A8 8 0 0 1 4.2 10L9 15v1a2 2 0 0 0 2 2zm6.9-2.5A2 2 0 0 0 16 16h-1v-3a1 1 0 0 0-1-1H8v-2h2a1 1 0 0 0 1-1V7h2a2 2 0 0 0 2-2v-.4a8 8 0 0 1 2.9 12.8z"/></svg>www.corvaleterracehotel.example</li>
    </ul>
    <div class="person">
      <div class="person__name">Elias Moreno</div>
      <div class="person__title">CEO/FOUNDER</div>
    </div>
    <div class="accent-bar"></div>
  </section>

  <section class="card card--back">
    <div class="back-name">CORVALE TERRACE HOTEL</div>
    <div class="back-web">www.corvaleterracehotel.example</div>
  </section>
</main>
</body>
</html>
```